Business Card Design - Photographer

I am a landscape photographer and I require a business card design. 

I require two designs:
1)  a double sided business card
 and
b)  a single sided business card 

The single sided design can either be the same as the double sided (with just one side having all the information)....or it can be an entire new design. Its up to you.

My corporate colours are (CMYK):

Blue   69, 32, 0, 0
Grey  72,  64,  47,  31
Green  32,  2,  91,  0
Yellow   0, 19, 92, 0
Orange  0, 39, 75, 0

Colour space in final file should be in CMYK.

The details that need to be included on the card:

- Use the provided Logo
- Name: Wiktor Baranowski
- Email:   sales@vistalumeworks.com.au
- Website:    vistalumeworks.com.au
- Twitter:    twitter.com/vistalumeworks
- Facebook:   facebook.com/vistalumeworks
- Mobile  0417 539 662

Please use the attached template to design the logo to the specified size, including the marked bleed lines. I have also attached my logo in PNG (transparent background) and ai format for you to use.

The final file should be:
- Photoshop version with layers so I can edit the name/text etc. All non vector files should be high resolution at 1039 x 697 pixels at 300 dpi.

I also require a file as:
- Vector based PDF

Anyway questions please contact me.

Thank you

Industry/Entity Type

Landscape

Logo styles of interest
Pictorial/Combination Logo
Abstract Logo
Wordmark Logo
Lettermark Logo
Requirements
Must have
• The details that need to be included on the card:

- Use the provided Logo
- Name: Wiktor Baranowski
- Email: sales@vistalumeworks.com.au
- Website: vistalumeworks.com.au
- Twitter: twitter.com/vistalumeworks
- Facebook: facebook.com/vistalumeworks
- Mobile 0417 539 662

```html
<!DOCTYPE html>
<html lang="en">
<head>
<meta charset="utf-8">
<title>Vista Lume Works – Business Card</title>
<link rel="stylesheet" href="https://fonts.googleapis.com/css2?family=Cinzel:wght@400&family=Source+Sans+3:wght@400;600;700&display=swap">
<style>
  :root {
    --backdrop: #2c3334;
    --card: #ffffff;
    --ink: #3a3d4d;
    --ink-soft: #4a4d5a;
    --rule: #c9c9c9;
    --orange: #f7a74a;
    --blue: #3d8fcf;
    --mark: #3a3d4d;
  }
  * { margin: 0; padding: 0; box-sizing: border-box; }
  html, body {
    width: 987px; height: 1200px; overflow: hidden;
    background: var(--backdrop);
    font-family: "Source Sans 3", "Myriad Pro", sans-serif;
    color: var(--ink);
  }
  .card {
    position: absolute;
    width: 790px; height: 450px;
    background: var(--card);
    border-radius: 28px;
    overflow: hidden;
  }
  .card--front { left: 93px; top: 95px; }
  .card--back { left: 91px; top: 637px; }

  .brand-dot {
    position: absolute;
    border-radius: 50%;
    background: var(--mark);
  }
  .card--front .brand-dot { left: 72px; top: 45px; width: 240px; height: 240px; }
  .card--back .brand-dot { left: 298px; top: 28px; width: 190px; height: 190px; }

  .divider {
    position: absolute; left: 353px; top: 45px;
    width: 2px; height: 242px; background: var(--rule);
  }

  .wordmark {
    font-family: "Cinzel", "Trajan Pro", serif;
    font-weight: 400;
    color: var(--ink);
    white-space: nowrap;
  }
  .wordmark__name { border-bottom: 2px solid var(--ink); }
  .wordmark__tag { letter-spacing: .18em; }

  .card--front .wordmark { position: absolute; left: 393px; top: 38px; }
  .card--front .wordmark__name { font-size: 26px; line-height: 30px; padding-bottom: 0; }
  .card--front .wordmark__tag { font-size: 11px; margin-top: 4px; }

  .card--back .wordmark {
    position: absolute; left: 0; right: 0; top: 262px; text-align: center;
  }
  .card--back .wordmark__name {
    display: inline-block; font-size: 51px; line-height: 60px; padding: 0 2px;
  }
  .card--back .wordmark__tag { font-size: 22px; margin-top: 12px; letter-spacing: .2em; }

  .person { position: absolute; left: 393px; top: 118px; }
  .person__name { font-size: 31px; font-weight: 700; line-height: 34px; color: var(--ink); }
  .person__role { font-size: 18px; line-height: 22px; color: var(--ink-soft); }

  .contact { position: absolute; left: 389px; top: 205px; list-style: none; }
  .contact li { font-size: 19px; line-height: 29px; color: var(--ink-soft); }
  .contact b { font-weight: 700; color: var(--ink); }

  .swoosh { position: absolute; left: 0; top: 0; }

  .social {
    position: absolute; left: 0; right: 0; top: 403px;
    text-align: center; font-size: 19px; color: var(--ink);
  }
  .social b { font-weight: 700; }
  .social .sep { margin: 0 8px; }

  .site {
    position: absolute; left: 0; right: 0; top: 396px;
    text-align: center; font-size: 27px; color: var(--ink);
  }
</style>
</head>
<body>
  <section class="card card--front">
    <div class="brand-dot"></div>
    <div class="divider"></div>
    <div class="wordmark">
      <div class="wordmark__name">VISTA LUME WORKS</div>
      <div class="wordmark__tag">FINE ART PHOTOGRAPHY</div>
    </div>
    <div class="person">
      <div class="person__name">Your Name</div>
      <div class="person__role">Adminsitrator</div>
    </div>
    <ul class="contact">
      <li><b>m</b> : 0417 539 662</li>
      <li><b>e</b> : sales@vistalumeworks.com.au</li>
      <li><b>w</b> : vistalumeworks.com.au</li>
    </ul>
    <svg class="swoosh" width="790" height="450" viewBox="0 0 790 450">
      <path fill="var(--blue)" d="M519,374 C630,366 730,318 790,238 L790,292 C730,338 640,368 540,374 Z"/>
      <path fill="var(--orange)" d="M0,405 C60,372 150,357 260,360 C380,364 480,377 560,374 C660,370 730,342 790,298 L790,450 L0,450 Z"/>
    </svg>
    <div class="social"><b>t</b> : twitter.com/vistalumeworks<span class="sep">|</span><b>f</b> : facebook.com/vistalumeworks</div>
  </section>

  <section class="card card--back">
    <div class="brand-dot"></div>
    <div class="wordmark">
      <div class="wordmark__name">VISTA LUME WORKS</div>
      <div class="wordmark__tag">FINE ART PHOTOGRAPHY</div>
    </div>
    <div class="site">www.vistalumeworks.com.au</div>
  </section>
</body>
</html>
```